Web Design for Webdesign company 3 page PSD

Project
---------
We need a PSD Web Design to be used in a WordPress installation.
What we would like to create is a professional looking website for a web design agency. We also need you to look for suitable stock images to be placed on these pages.
We need the design for:
Homepage
Landing page
Contact page
attached in the pages file you will find a file with more in depth details how these files should be build up.
We would like to see a desktop version and a mobile version of these pages
The website should have a 1100px width.
The mobile design should have 480px width.
The homepage should have a header slider about 450px high.
The slider is preferred full width and should have some images text and a button
Objectives
-------------
The main objective for the website is to get leads from customers in the form of a request for a quotation or a call or mail me back action. The most important action for the homepage is to link and navigate to our landing pages.
What we want to tell our visitors (our main products)
-------------------------------------------------------------------
- A website with no big investment but a monthly rate
- A successful website with no worries (a complete website, seo, hosting and a service contract for future customization is included for a monthly rate)
Color Scheme
------------
Use branding colors. You can find them in the branding.pdf file.
Additional colors:
White: #ffffff
Black: #181818
Company info
--------------
We are a starting web design / marketing agency based in The Netherlands and looking for the design of our website. Our services are (custom) webdesign, website marketing or combinations of both. Our main customer group is small business owners.
We sell websites but give the option to buy it with a lease contract.
A second product is a default website with a complete service: SEO, hosting and a service contract for a monthly rate.
Content:
-----------
If not available place Lorem Ipsum text.
There will come about 400 words of text on the landing pages
Design Competition
--------------------------
Since this is a designing competition we would like to see your creativity.
What you can expect from us is a lot of feedback 7 days a week with short response time.
You can send us the first sketchy mock ups of the homepage and we will give feedback based on these design. But we like your feedback or comments as well
Read the pages file for more in depth details how the pages should be designed

Target Market(s)
Small business owners in The Netherlands
Industry/Entity Type
It Company
Number of Pages Required
3 page
Requirements
Must have
- Homepage:
- Header slider with images, some text and a link to a custom page
- The slider should have 3 designed slides
- Landings page:
- Sidebar
- Action button for a request for a quotation
- Action button for a call me back action
- Action button for an appointment
- Contact form:
- Address details
- Contact form
Nice to have
- Homepage:
- Full width slider
- Testimonial block
- Blog items
Should not have
- Flash
- A to crowded design

```html
<!DOCTYPE html>
<html lang="en">
<head>
<meta charset="utf-8">
<title>Birchline Web Studio – Custom Web Design</title>
<link href="https://fonts.googleapis.com/css2?family=Roboto:wght@300;400;500;700&display=swap" rel="stylesheet">
<style>
:root{
  --blue:#27b0df;
  --green:#5f9c7c;
  --green-text:#4d8a6c;
  --black:#181818;
  --header:#1c1c1c;
  --footer:#1f1f1f;
  --white:#ffffff;
  --text:#666666;
  --line:#dddddd;
  --muted:#c8c8c8;
}
*{box-sizing:border-box;margin:0;padding:0}
html,body{width:1072px;height:1200px;overflow:hidden}
body{font-family:'Roboto',Arial,sans-serif;background:var(--white);position:relative;color:var(--text)}
.site-header{position:absolute;left:0;top:0;width:1072px;height:101px;background:var(--header)}
.brand{position:absolute;left:67px;top:34px;display:flex;align-items:center;gap:10px;color:var(--white)}
.brand-mark{width:32px;height:32px;border-radius:50%;background:var(--white)}
.brand-name{font-weight:500;font-size:18px;line-height:1}
.calc-link{position:absolute;left:569px;top:36px;display:flex;align-items:center;gap:8px;color:var(--blue);font-weight:500;font-size:17px;text-decoration:none}
.quote-btn{position:absolute;left:815px;top:27px;width:191px;height:47px;background:var(--green);color:var(--white);font-weight:500;font-size:17px;display:flex;align-items:center;justify-content:center;text-decoration:none}
.hero{position:absolute;left:0;top:101px;width:1072px;height:371px;background:linear-gradient(120deg,#6a4a3c 0%,#7a3a3a 30%,#4b4560 60%,#2b3350 100%);text-align:center}
.hero h1{position:absolute;left:0;right:0;top:102px;font-size:45px;font-weight:500;color:var(--blue);letter-spacing:.5px}
.hero p{position:absolute;left:100px;right:100px;top:162px;font-size:37px;font-weight:500;line-height:40px;color:var(--white);letter-spacing:.3px}
.side-nav{position:absolute;left:67px;top:511px;width:216px;border:1px solid var(--line);list-style:none}
.side-nav li{height:42px;border-top:1px solid var(--line);background:#f7f7f7;display:flex;align-items:center;justify-content:space-between;padding:0 14px;font-size:12.5px;color:var(--green-text);letter-spacing:.3px}
.side-nav li:first-child{border-top:none}
.side-nav li.active{background:var(--white);color:var(--black)}
.actions{position:absolute;left:67px;top:783px;width:216px}
.action{display:flex;height:39px;margin-bottom:6px;text-decoration:none}
.action .icon{width:31px;background:var(--black);display:flex;align-items:center;justify-content:center}
.action .label{flex:1;background:var(--blue);color:var(--white);font-weight:500;font-size:13px;display:flex;align-items:center;justify-content:space-between;padding:0 8px 0 10px}
.content{position:absolute;left:324px;top:505px;width:682px}
.content h2{font-size:25px;font-weight:500;color:var(--blue);letter-spacing:.4px;margin-bottom:10px}
.content p{font-size:12px;line-height:21.5px;font-weight:300;color:#555;letter-spacing:.15px}
.block-techniques{position:absolute;left:324px;top:657px;width:682px}
.block-portfolio{position:absolute;left:324px;top:788px;width:682px}
.portfolio{display:flex;gap:17px;margin-top:16px}
.portfolio .shot{width:216px;height:120px}
.site-footer{position:absolute;left:0;top:999px;width:1072px;height:201px;background:var(--footer);color:var(--muted)}
.site-footer h3{font-size:19px;font-weight:500;color:var(--blue);letter-spacing:.3px}
.col-blog{position:absolute;left:67px;top:29px;width:275px}
.col-blog .post-title{color:var(--green);font-size:12.5px;margin-top:12px}
.col-blog p{font-size:11.5px;line-height:19px;font-weight:300;margin-top:4px}
.col-blog a{display:block;color:var(--blue);font-size:10.5px;font-style:italic;margin-top:7px;text-decoration:none}
.divider{position:absolute;top:32px;width:1px;height:132px;background:#3a3a3a}
.col-company{position:absolute;left:425px;top:29px}
.col-company ul{list-style:none;display:grid;grid-template-columns:89px auto;row-gap:10px;margin-top:12px;font-size:11.5px;font-weight:300}
.col-connect{position:absolute;left:703px;top:29px;width:250px}
.socials{display:flex;gap:6px;margin-top:12px}
.socials span{width:26px;height:26px;border-radius:50%;background:#9a9a9a}
.copy{display:flex;align-items:center;gap:18px;margin-top:26px;font-size:10.5px;line-height:16px;font-weight:300}
.copy .foot-mark{width:26px;height:26px;border-radius:50%;background:#777;margin-left:4px;margin-right:22px}
</style>
</head>
<body>

<header class="site-header">
  <div class="brand">
    <span class="brand-mark"></span>
    <span class="brand-name">Birchline Web Studio</span>
  </div>
  <a class="calc-link" href="#">
    <svg width="28" height="28" viewBox="0 0 28 28" aria-hidden="true"><rect x="4" y="2" width="20" height="24" rx="2" fill="#e8e8e8" transform="rotate(-12 14 14)"/><rect x="8" y="5" width="12" height="5" fill="#7ab0c8" transform="rotate(-12 14 14)"/><g fill="#777" transform="rotate(-12 14 14)"><rect x="8" y="13" width="3" height="3"/><rect x="12.5" y="13" width="3" height="3"/><rect x="17" y="13" width="3" height="3"/><rect x="8" y="18" width="3" height="3"/><rect x="12.5" y="18" width="3" height="3"/><rect x="17" y="18" width="3" height="3"/></g></svg>
    Calculate Design Cost
  </a>
  <a class="quote-btn" href="#">Request a Quotation</a>
</header>

<section class="hero" role="img" aria-label="Photo of a desk with a tablet showing a web page, a coffee cup and hands sketching on paper">
  <h1>Custom Web Design</h1>
  <p>Contains content over web design fully custom and template design</p>
</section>

<ul class="side-nav">
  <li>Approach<svg width="7" height="11" viewBox="0 0 7 11"><path d="M1 1l4.5 4.5L1 10" fill="none" stroke="#555" stroke-width="1.2"/></svg></li>
  <li class="active">Web Design<svg width="7" height="11" viewBox="0 0 7 11"><path d="M1 1l4.5 4.5L1 10" fill="none" stroke="#555" stroke-width="1.2"/></svg></li>
  <li>Technique<svg width="7" height="11" viewBox="0 0 7 11"><path d="M1 1l4.5 4.5L1 10" fill="none" stroke="#555" stroke-width="1.2"/></svg></li>
  <li>Modules<svg width="7" height="11" viewBox="0 0 7 11"><path d="M1 1l4.5 4.5L1 10" fill="none" stroke="#555" stroke-width="1.2"/></svg></li>
  <li>Generate Traffic<svg width="7" height="11" viewBox="0 0 7 11"><path d="M1 1l4.5 4.5L1 10" fill="none" stroke="#555" stroke-width="1.2"/></svg></li>
  <li>Increase Conversion<svg width="7" height="11" viewBox="0 0 7 11"><path d="M1 1l4.5 4.5L1 10" fill="none" stroke="#555" stroke-width="1.2"/></svg></li>
</ul>

<div class="actions">
  <a class="action" href="#"><span class="icon"><svg width="18" height="18" viewBox="0 0 18 18"><path d="M1 8l16-7-6 16-3-6z M8 11l9-10" fill="none" stroke="#fff" stroke-width="1.2"/></svg></span><span class="label">Visit Contact Us Page<svg width="14" height="14" viewBox="0 0 14 14"><circle cx="7" cy="7" r="7" fill="#fff"/><path d="M5.5 4v6l4-3z" fill="#333"/></svg></span></a>
  <a class="action" href="#"><span class="icon"><svg width="18" height="18" viewBox="0 0 18 18"><path d="M4 1l3 4-2 2c1 2 3 4 5 5l2-2 4 3-2 3C8 16 2 10 1 4z" fill="none" stroke="#fff" stroke-width="1.2"/></svg></span><span class="label">Call Me Back<svg width="14" height="14" viewBox="0 0 14 14"><circle cx="7" cy="7" r="7" fill="#fff"/><path d="M5.5 4v6l4-3z" fill="#333"/></svg></span></a>
  <a class="action" href="#"><span class="icon"><svg width="18" height="18" viewBox="0 0 18 18"><rect x="1.5" y="3" width="15" height="13" fill="none" stroke="#fff" stroke-width="1.2"/><path d="M1.5 7h15M5 1v4M13 1v4" stroke="#fff" stroke-width="1.2"/><g fill="#fff"><rect x="4" y="9" width="2" height="2"/><rect x="8" y="9" width="2" height="2"/><rect x="12" y="9" width="2" height="2"/><rect x="4" y="12.5" width="2" height="2"/><rect x="8" y="12.5" width="2" height="2"/></g></svg></span><span class="label">Make an Appointment<svg width="14" height="14" viewBox="0 0 14 14"><circle cx="7" cy="7" r="7" fill="#fff"/><path d="M5.5 4v6l4-3z" fill="#333"/></svg></span></a>
  <a class="action" href="#"><span class="icon"><svg width="18" height="18" viewBox="0 0 18 18"><path d="M5 4h9v13H5z M3 2h9v2" fill="none" stroke="#fff" stroke-width="1.2"/><path d="M7 8h5M7 11h5M7 14h3" stroke="#fff" stroke-width="1.2"/></svg></span><span class="label">Request a Quotation<svg width="14" height="14" viewBox="0 0 14 14"><circle cx="7" cy="7" r="7" fill="#fff"/><path d="M5.5 4v6l4-3z" fill="#333"/></svg></span></a>
</div>

<section class="content">
  <h2>Web Design</h2>
  <p>Aliquam molestie, mi et imperdiet euismod, dui purus auctor tellus, et interdum lacus lectus et ante. Sed accumsan sollicitudin sapien, sit amet adipiscing turpis gravida ac. In congue, neque ac lobortis volutpat, libero mauris varius mi, vitae suscipit ipsum ligula vitae risus. Duis aliquam nibh a dui iaculis viverra id a velit. Vivamus egestas risus in magna varius commodo. Sed semper viverra egestas. Etiam pretium porttitor lectus, vel ornare neque porta volutpat...</p>
</section>

<section class="content block-techniques">
  <h2>Latest Techniques</h2>
  <p>Aliquam molestie, mi et imperdiet euismod, dui purus auctor tellus, et interdum lacus lectus et ante. Sed accumsan sollicitudin sapien, sit amet adipiscing turpis gravida ac. In congue, neque ac lobortis volutpat, libero mauris varius mi, vitae suscipit ipsum ligula vitae risus. Duis aliquam nibh a dui iaculis viverra id a velit.</p>
</section>

<section class="content block-portfolio">
  <h2>Our Portfolio</h2>
  <div class="portfolio">
    <div class="shot" role="img" aria-label="Website screenshot for a handyman service in yellow and white" style="background:linear-gradient(135deg,#2a2a2a 0%,#d9a520 35%,#e8e2d8 70%,#c9b79a 100%)"></div>
    <div class="shot" role="img" aria-label="Website screenshot for a marketing company in bright green" style="background:linear-gradient(135deg,#1e1e1e 0%,#4f9a1c 30%,#6cb52a 70%,#f2f2f2 100%)"></div>
    <div class="shot" role="img" aria-label="Website screenshot for a cooking recipe site with fresh vegetables" style="background:linear-gradient(135deg,#6b3a1a 0%,#4a7a2a 40%,#d04a2a 65%,#f4efe6 100%)"></div>
  </div>
</section>

<footer class="site-footer">
  <div class="col-blog">
    <h3>Blog Post</h3>
    <div class="post-title">Aliquam molestiemi et imperdiet euismod..</div>
    <p>Dui purus auctor tellus, et interdum lacus lectus et ante. Sed accumsan sollicitudin sapien, sit amet adipiscing turpis gravida ac.</p>
    <a href="#">Continue Reading</a>
  </div>
  <div class="divider" style="left:385px"></div>
  <div class="col-company">
    <h3>Company</h3>
    <ul>
      <li>Home</li><li>Blog</li>
      <li>About Us</li><li>Testimonials</li>
      <li>Services</li><li>Contact Us</li>
      <li>Projects</li>
    </ul>
  </div>
  <div class="divider" style="left:666px"></div>
  <div class="col-connect">
    <h3>Connect Us</h3>
    <div class="socials"><span></span><span></span><span></span><span></span></div>
    <div class="copy">
      <span class="foot-mark"></span>
      <div>Copyright © 2015. Company Name.<br>All Right Reserved</div>
    </div>
  </div>
</footer>

</body>
</html>
```